International business needs business cards

Our company, DRV Ventures Inc. is in the business of supplying a range construction products with particular emphasis on CEMENT. We have developed our own brand - TORVAN SUPPLIES - with which to infiltrate the market. We are launching our brand of cement (TORVAN Type IS Cement) into the Caribbean which is unlike anything this market has ever seen. A monopoly has existed here for the past 60-odd years and the market has now opened to allow the importation of other brands and consumers are anxious and ready for change/improvement. We are very excited to be launching and want to make a great first impression. We will be conducting workshops and seminars (from government level to the hardware store owners) and we want our business card to give us the strong, confident introduction that we need.

Target Market(s)

construction; builders; engineers; home owners

Industry/Entity Type

Construction

Contact Information for Business Card

Marisol Depree
CEO
cell # 1 555 4180736
Ground floor,Lindell Plaza Suite 2734
George Town,Grand Cayman
Cayman Islands,KY1-4823
EMAIL: m.depree@drvventuresinc.example
web site drvventuresinc.example

COMPANY: skype info drv.ventures.example

second card
Yvette Brannock-Depree
CFO
CELL# 1 555 607 3941
George Town,Grand Cayman
Cayman Islands,KY1-4823
EMAIL: y.brannockdepree@drvventuresinc.example
website drvventuresinc.example

Requirements
Must have
• Business cards must display BOTH logos - DRV is the company and TORVAN is the brand.

```html
<!DOCTYPE html>
<html lang="en">
<head>
<meta charset="utf-8">
<title>DRV Ventures Inc. – Business Card</title>
<link href="https://fonts.googleapis.com/css2?family=Source+Sans+3:wght@400;600&display=swap" rel="stylesheet">
<style>
  :root {
    --backdrop: #3a322e;
    --card: #121212;
    --card-edge: #1c1c1c;
    --brand-red: #8e1b1b;
    --accent-red: #b3241f;
    --text-light: #e4e4e4;
    --text-muted: #bdbdbd;
    --silver: #8a8a8a;
    --rule: #555;
  }
  * { box-sizing: border-box; margin: 0; padding: 0; }
  html, body { width: 1200px; height: 814px; overflow: hidden; }
  body {
    background: var(--backdrop);
    font-family: "Source Sans 3", "Myriad Pro", sans-serif;
    position: relative;
  }
  .card {
    position: absolute;
    top: 252px;
    width: 540px;
    height: 309px;
    background: var(--card);
    border: 1px solid var(--card-edge);
    box-shadow: 0 8px 24px rgba(0,0,0,.45);
  }
  .card--front { left: 40px; }
  .card--back { left: 620px; }

  .brand {
    position: absolute;
    display: flex;
    align-items: center;
    gap: 10px;
  }
  .brand__mark {
    width: 66px; height: 66px;
    background: var(--brand-red);
    flex: none;
  }
  .brand__name {
    color: #fff;
    font-weight: 600;
    font-size: 25px;
    line-height: 1.05;
    width: 120px;
  }
  .card--front .brand { left: 36px; top: 148px; }

  .divider {
    position: absolute;
    left: 262px; top: 40px;
    width: 1px; height: 210px;
    background: linear-gradient(to bottom, transparent, var(--rule) 20%, var(--rule) 80%, transparent);
  }

  .contact {
    position: absolute;
    left: 282px; top: 48px;
    color: var(--text-light);
    font-size: 15px;
    line-height: 1.28;
  }
  .contact__name { color: var(--accent-red); font-size: 17px; }
  .contact__role { margin-bottom: 6px; }
  .contact__address { margin-bottom: 8px; }
  .contact__line { display: flex; align-items: center; gap: 7px; }
  .contact__line svg { width: 12px; height: 12px; flex: none; }

  .product-brand {
    position: absolute;
    left: 56px; top: 58px;
    width: 190px;
    display: flex;
    flex-direction: column;
    align-items: center;
    gap: 12px;
  }
  .product-brand__mark {
    width: 96px; height: 96px;
    border-radius: 50%;
    background: #4a4a4a;
  }
  .product-brand__name {
    color: var(--silver);
    font-weight: 600;
    font-size: 20px;
    letter-spacing: 2px;
    text-align: center;
    line-height: 1.1;
  }

  .card--back .brand { left: 290px; top: 70px; }
  .card--back .brand__mark { width: 58px; height: 58px; }
  .card--back .brand__name { font-size: 23px; }
  .web {
    position: absolute;
    left: 262px; top: 222px;
    color: var(--text-muted);
    font-size: 14px;
    letter-spacing: 1.5px;
  }
</style>
</head>
<body>
  <section class="card card--front">
    <div class="brand">
      <div class="brand__mark"></div>
      <div class="brand__name">DRV Ventures Inc.</div>
    </div>
    <div class="divider"></div>
    <div class="contact">
      <div class="contact__name">Marisol Depree</div>
      <div class="contact__role">CEO</div>
      <div class="contact__address">
        Ground floor<br>
        Lindell Plaza Suite 2734<br>
        George Town,Grand Cayman<br>
        Cayman Islands,KY1-4823
      </div>
      <div class="contact__line">
        <svg viewBox="0 0 12 12"><rect x="3" y="0.5" width="6" height="11" rx="1" fill="none" stroke="#b3241f" stroke-width="1.4"/><circle cx="6" cy="9.3" r="0.8" fill="#b3241f"/></svg>
        1 555 4180736
      </div>
      <div class="contact__line">
        <svg viewBox="0 0 12 12"><rect x="0.5" y="2" width="11" height="8" fill="#b3241f"/><path d="M0.5 2 L6 6.5 L11.5 2" fill="none" stroke="#121212" stroke-width="1"/></svg>
        m.depree@drvventuresinc.example
      </div>
      <div class="contact__line">
        <svg viewBox="0 0 12 12"><circle cx="6" cy="6" r="5.5" fill="#b3241f"/><path d="M0.5 6 H11.5 M6 0.5 C3 3 3 9 6 11.5 M6 0.5 C9 3 9 9 6 11.5" fill="none" stroke="#121212" stroke-width="0.8"/></svg>
        drvventuresinc.example
      </div>
    </div>
  </section>

  <section class="card card--back">
    <div class="product-brand">
      <div class="product-brand__mark"></div>
      <div class="product-brand__name">TORVAN SUPPLIES</div>
    </div>
    <div class="brand">
      <div class="brand__mark"></div>
      <div class="brand__name">DRV Ventures Inc.</div>
    </div>
    <div class="web">www.drvventuresinc.example</div>
  </section>
</body>
</html>
```